Launch Website

A very simple, but attractive website (template preferred) is required in a common format - HTML5 or Wordpress etc.
It should be easily user updateable for updates.
Pages it needs:
-Home Page with menu bar, company logo and 1 large graphic/picture and two smaller graphics/logos.
- What we do
- How we do it
- About Us
- Guarantees
- Results
- Contact Page with Enquiry Form
- Provision for a blog to be added later

Most pages will be approx 150 words text with some small/medium images.
We have our own domain & hosting.

A "less is more" design approach would be encouraged.

Target Market(s)

Vehicle Fleet Managers

Industry/Entity Type

It Company

Font styles to use
Sans Serif

Colors
9bcb3c

Requirements
Must have
• Corporate Style. No Fluff.
Nice to have
• Images of LIght Commerical vehicles and trucks

Am ok with white background throughout site.
Colours should match/complement company logo.
Should not have
• Should not be too "busy"

```html
<!DOCTYPE html>
<html lang="en">
<head>
<meta charset="utf-8">
<title>Clearline Tune – Diesel Fleet Engine Optimisation</title>
<link rel="stylesheet" href="https://fonts.googleapis.com/css2?family=Open+Sans:wght@400;600&family=Roboto+Condensed:wght@400;700&display=swap">
<style>
  :root {
    --brand-blue: #1e9bd7;
    --band-top: #1b5a93;
    --band-bottom: #124573;
    --ink: #222222;
    --muted: #8a8a8a;
    --rule: #d6d6d6;
    --accent-red: #e3161d;
    --footer-bg: #efefef;
    --button-bg: #c9c9c9;
    --panel-black: #050505;
    --photo-top: #c3cad2;
    --photo-bottom: #e6e9ec;
  }
  * { box-sizing: border-box; margin: 0; padding: 0; }
  html, body { width: 1200px; height: 1003px; overflow: hidden; }
  body {
    position: relative;
    background: #ffffff;
    font-family: "Open Sans", Arial, sans-serif;
    color: var(--ink);
  }

  .site-header {
    position: absolute; left: 0; top: 0; width: 1200px; height: 102px;
    background: linear-gradient(#ffffff, #f1f1f1);
  }
  .brand {
    position: absolute; left: 131px; top: 34px;
    display: flex; align-items: center; gap: 10px;
    font-family: "Open Sans", Arial, sans-serif;
    font-weight: 600; font-size: 28px; color: var(--band-top);
    letter-spacing: -0.5px;
  }
  .brand-dot { width: 18px; height: 18px; border-radius: 50%; background: var(--brand-blue); }
  .contact {
    position: absolute; right: 132px; top: 24px;
    display: flex; align-items: center; gap: 8px;
  }
  .contact-lines { text-align: left; font-size: 14px; color: var(--muted); line-height: 20px; }
  .contact-lines .phone { color: var(--accent-red); font-size: 20px; font-weight: 600; }
  .contact-lines .email { color: var(--ink); }

  .hero-band {
    position: absolute; left: 0; top: 102px; width: 1200px; height: 442px;
    background: linear-gradient(var(--band-top), var(--band-bottom));
  }
  .main-nav {
    position: absolute; left: 157px; top: 116px; width: 886px;
    display: flex; justify-content: space-between;
    font-family: "Roboto Condensed", Arial, sans-serif;
    font-size: 15px; font-weight: 700; color: #ffffff;
    text-transform: uppercase; letter-spacing: 0.2px;
  }

  .hero-panel {
    position: absolute; left: 131px; top: 154px; width: 937px; height: 470px;
    background: #ffffff; border-radius: 3px;
    box-shadow: 0 18px 14px -12px rgba(0,0,0,0.35);
  }
  .hero-photo {
    position: absolute; left: 9px; top: 10px; width: 920px; height: 449px;
    background: linear-gradient(180deg, var(--photo-top) 0%, var(--photo-bottom) 100%);
  }
  .hero-callout {
    position: absolute; left: 541px; top: 64px; width: 366px; height: 174px;
    background: var(--panel-black);
    border-left: 6px solid var(--brand-blue);
    border-bottom: 5px solid var(--brand-blue);
    font-family: "Roboto Condensed", Arial, sans-serif;
    color: #ffffff; text-align: right; padding: 22px 26px 0 0;
  }
  .hero-callout .lead { font-size: 24px; line-height: 28px; }
  .hero-callout .save { font-size: 20px; color: var(--brand-blue); text-align: left; padding-left: 72px; }
  .hero-callout .figure { font-size: 50px; font-weight: 700; color: var(--brand-blue); line-height: 46px; text-align: left; padding-left: 72px; }
  .hero-callout .figure small { font-size: 32px; }
  .hero-callout .tail { font-size: 24px; line-height: 30px; }
  .partner-badge {
    position: absolute; top: 366px; width: 128px; height: 75px;
    background: #ffffff; border: 1px solid #e4e4e4;
  }
  .partner-badge.one { left: 643px; }
  .partner-badge.two { left: 781px; }
  .slider-dots { position: absolute; left: 28px; top: 432px; display: flex; gap: 4px; }
  .slider-dots span { width: 10px; height: 10px; background: #ffffff; }
  .slider-dots span.active { background: var(--brand-blue); }

  .features {
    position: absolute; left: 131px; top: 680px; width: 937px;
    display: flex; justify-content: space-between;
  }
  .feature { width: 206px; }
  .feature h2 {
    font-family: "Roboto Condensed", Arial, sans-serif;
    font-weight: 400; font-size: 21px; color: var(--brand-blue);
    padding-bottom: 6px; border-bottom: 1px solid var(--rule); position: relative;
  }
  .feature h2::after {
    content: ""; position: absolute; left: 0; bottom: -1px; width: 76px; height: 3px;
    background: var(--brand-blue);
  }
  .feature p { margin-top: 16px; font-size: 12.6px; line-height: 18.7px; color: var(--muted); height: 94px; }
  .read-more {
    display: inline-block; margin-top: 10px; width: 76px; height: 24px; line-height: 24px;
    text-align: center; font-size: 11px; color: #ffffff; background: var(--button-bg); border-radius: 2px;
  }

  .site-footer {
    position: absolute; left: 0; top: 923px; width: 1200px; height: 80px;
    background: var(--footer-bg);
  }
  .legal { position: absolute; left: 131px; top: 21px; font-size: 13px; line-height: 19px; color: var(--muted); }
  .social { position: absolute; left: 960px; top: 25px; display: flex; gap: 10px; }
  .social span { width: 29px; height: 29px; background: var(--band-top); }
</style>
</head>
<body>
  <header class="site-header">
    <div class="brand"><span class="brand-dot"></span>Clearline Tune</div>
    <div class="contact">
      <svg width="44" height="56" viewBox="0 0 44 56" aria-hidden="true">
        <path d="M14 4 C6 8 4 22 10 34 C14 42 20 46 26 44" fill="none" stroke="#222" stroke-width="5" stroke-linecap="round"/>
        <path d="M24 44 C32 48 40 46 38 54" fill="none" stroke="#222" stroke-width="1.5"/>
      </svg>
      <div class="contact-lines">
        <div>Contact us on <span class="phone">(02) 5550 1234</span></div>
        <div>or email us <span class="email">hello@clearlinetune.com</span></div>
      </div>
    </div>
  </header>

  <div class="hero-band"></div>
  <nav class="main-nav">
    <span>Home</span><span>What we do</span><span>How we do it</span><span>About us</span>
    <span>Guarantees</span><span>Results</span><span>Testimonials</span><span>Contact</span><span>Blog</span>
  </nav>

  <section class="hero-panel">
    <div class="hero-photo" role="img" aria-label="Photograph of a convoy of heavy haulage trucks on a snowy road"></div>
    <div class="hero-callout">
      <div class="lead">We help diesel vehicle fleets</div>
      <div class="save">save up to</div>
      <div class="figure">20% <small>FUEL COSTS</small></div>
      <div class="tail">by optimising their engines.</div>
    </div>
    <div class="partner-badge one" role="img" aria-label="Industry association membership badge"></div>
    <div class="partner-badge two" role="img" aria-label="Partner badge"></div>
    <div class="slider-dots"><span class="active"></span><span></span><span></span></div>
  </section>

  <section class="features">
    <article class="feature">
      <h2>ABOUT US</h2>
      <p>Steadyway Fleet have combined over 50 years experience in all aspects of the automotive industry including commercial fleet and diesel engines. We are the ...</p>
      <span class="read-more">Read More</span>
    </article>
    <article class="feature">
      <h2>WHAT WE DO</h2>
      <p>Steadyway Fleet delivers award winning, ISO 9001 certified diesel engine ECU remapping for fleet operations. As Principal Australian Fleet Agent for Clearline...</p>
      <span class="read-more">Read More</span>
    </article>
    <article class="feature">
      <h2>HOW WE DO IT</h2>
      <p>Steadyway Fleet will conduct an obligation Free Consultation with your Fleet Representatives to determine your Fleets needs, and identify any customization...</p>
      <span class="read-more">Read More</span>
    </article>
    <article class="feature">
      <h2>WHY</h2>
      <p>We've acted on customer requests for cost effective, financially attractive solutions to reduce fuel and operating costs whilst also reducing environmental foot...</p>
      <span class="read-more">Read More</span>
    </article>
  </section>

  <footer class="site-footer">
    <div class="legal">Copyright 2014 Clearline Tune. All Rights Reserved.<br>Privacy Policy | Terms and Conditions</div>
    <div class="social" aria-label="Social links"><span></span><span></span><span></span></div>
  </footer>
</body>
</html>
```